BildeVOLD buisnesscard

Hey :) I need a modern buisnesscard for my company BildeVOLD
It most have:
Dagligleder og Fotograf: Henrik Audun Strandvik

Mob: +4791264085
Epost: post@bildevold.example
Adresse: Kvernbakken9, 6040 Strandeid

Facbook and instagram logo with text BildeVOLD

BildeVOLD logo

It Company

```html
<!DOCTYPE html>
<html lang="no">
<head>
<meta charset="utf-8">
<title>BildeVOLD – visittkort</title>
<link href="https://fonts.googleapis.com/css2?family=Montserrat:wght@400;500;700;800&display=swap" rel="stylesheet">
<style>
  :root {
    --bg: #2b2b2b;
    --card-black: #000000;
    --card-white: #ffffff;
    --card-grey: #b3b3b3;
    --brand-grey: #a6a6a6;
    --ink: #111111;
    --ink-soft: #ffffff;
    --divider: #000000;
  }
  * { margin: 0; padding: 0; box-sizing: border-box; }
  html, body { width: 1200px; height: 900px; overflow: hidden; }
  body {
    background: var(--bg);
    font-family: "Montserrat", sans-serif;
    position: relative;
  }
  .card {
    position: absolute;
    top: 295px;
    width: 540px;
    height: 310px;
    border-radius: 22px;
    overflow: hidden;
  }
  /* Front */
  .card-front {
    left: 40px;
    background: var(--card-black);
    display: flex;
    flex-direction: column;
    align-items: center;
    justify-content: center;
  }
  .front-wordmark {
    font-weight: 800;
    font-size: 54px;
    color: var(--brand-grey);
    letter-spacing: -1px;
    margin-top: -10px;
  }
  .front-handle {
    position: absolute;
    bottom: 34px;
    left: 0; right: 0;
    display: flex;
    flex-direction: column;
    align-items: center;
    gap: 6px;
  }
  .handle-mark {
    width: 10px; height: 10px;
    background: var(--brand-grey);
  }
  .handle-name {
    font-size: 13px;
    font-weight: 400;
    color: var(--brand-grey);
  }
  /* Back */
  .card-back {
    left: 620px;
    display: flex;
  }
  .back-brand {
    width: 50%;
    background: var(--card-white);
    display: flex;
    align-items: center;
    justify-content: center;
    border-right: 2px solid var(--divider);
  }
  .back-wordmark {
    font-weight: 800;
    font-size: 38px;
    color: var(--brand-grey);
    letter-spacing: -0.5px;
  }
  .back-contact {
    width: 50%;
    background: var(--card-grey);
    padding: 72px 22px 0 10px;
    text-align: right;
    color: var(--ink);
  }
  .contact-name {
    font-weight: 700;
    font-size: 15px;
  }
  .contact-title {
    font-size: 11px;
    color: var(--ink-soft);
    margin-top: 2px;
  }
  .contact-icons {
    display: flex;
    justify-content: flex-end;
    gap: 4px;
    margin: 6px 0 4px;
  }
  .contact-icons svg { width: 9px; height: 9px; }
  .contact-line {
    font-size: 12.5px;
    line-height: 1.35;
  }
</style>
</head>
<body>
  <section class="card card-front">
    <div class="front-wordmark">BildeVOLD</div>
    <div class="front-handle">
      <span class="handle-mark"></span>
      <span class="handle-name">BildeVOLD</span>
    </div>
  </section>

  <section class="card card-back">
    <div class="back-brand">
      <div class="back-wordmark">BildeVOLD</div>
    </div>
    <div class="back-contact">
      <div class="contact-name">Henrik Audun Strandvik</div>
      <div class="contact-title">Dagligleder og Fotograf</div>
      <div class="contact-icons">
        <svg viewBox="0 0 10 10" aria-label="telefon"><path d="M2 1 L4 1 L4.6 3 L3.5 3.8 Q4.5 5.8 6.2 6.5 L7 5.4 L9 6 L9 8 Q5 9 2 4.5 Q1.3 2.5 2 1Z" fill="#fff"/></svg>
        <svg viewBox="0 0 10 10" aria-label="e-post"><rect x="0.8" y="2" width="8.4" height="6" fill="none" stroke="#fff" stroke-width="1"/><path d="M0.8 2 L5 5.5 L9.2 2" fill="none" stroke="#fff" stroke-width="1"/></svg>
        <svg viewBox="0 0 10 10" aria-label="adresse"><path d="M5 9.5 L2 5 A3 3 0 1 1 8 5 Z" fill="#fff"/><circle cx="5" cy="3.8" r="1.1" fill="#b3b3b3"/></svg>
      </div>
      <div class="contact-line">+4791264085</div>
      <div class="contact-line">post@bildevold.example</div>
      <div class="contact-line">Kvernbakken9, 6040 Strandeid</div>
    </div>
  </section>
</body>
</html>
```